Dynamic Business Card for Sports Supplements Company

Hi! I'm looking for an awesome business card to match my existing sports supplement company. I have uploaded my current company logo and screenshot of the front page of my website.

I would like to have something dynamic and interesting and utilize the colors in the website - the reds and purples

The business card should be double sided and focus on a unique eye-catching design on the back and include all the relevant company info.

Most importantly, it should say somewhere: "Sign up on our website for a coupon code."

Target Market(s)

Mostly for women gym goers but it shouldn't be too feminine. It should be in keeping with the website design. It should flow and clearly be connected to it

Industry/Entity Type

Business

Contact Information for Business Card

Lorraine K. Vestal
CEO
LVestal@Quorvanexco.com
www.quorvanexco.com
555.417.3820
P.O. Box 47315
Harlow, Vermont 00000

Sign up on our website for a coupon code

Font styles to use
Serif
Sans Serif
Other font styles liked:
• Novecento font family and "Quorvanex" is in AR Destine font

Requirements
Must have
• One side should be a bold Quorvanex logo design. Even just the symbol itself may be o.k. (see attached file)

```html
<!DOCTYPE html>
<html lang="en">
<head>
<meta charset="utf-8">
<title>Quorvanex Business Card</title>
<link href="https://fonts.googleapis.com/css2?family=Roboto:wght@300;400;900&display=swap" rel="stylesheet">
<style>
  :root {
    --bg: #e9e6e1;
    --card-black: #111111;
    --card-black-light: #2a2a2a;
    --red: #e8222b;
    --red-dark: #c9141d;
    --red-light: #f04a50;
    --white: #ffffff;
    --grey: #8a8a8a;
    --text-light: #e6e6e6;
  }
  * { margin: 0; padding: 0; box-sizing: border-box; }
  html, body { width: 1200px; height: 950px; overflow: hidden; }
  body {
    background: var(--bg);
    font-family: "Roboto", Arial, sans-serif;
    position: relative;
  }
  .card {
    position: absolute;
    left: 220px;
    width: 760px;
    height: 434px;
    overflow: hidden;
    box-shadow: 0 8px 24px rgba(0,0,0,.18);
  }
  .card-front {
    top: 30px;
    background: linear-gradient(135deg, var(--card-black-light) 0%, var(--card-black) 45%, #000 100%);
    color: var(--text-light);
  }
  .card-back {
    top: 486px;
    background: linear-gradient(135deg, var(--red-light) 0%, var(--red) 45%, var(--red-dark) 100%);
    color: var(--white);
  }

  /* front */
  .edge-strip {
    position: absolute; right: 0; top: 0; width: 22px; height: 100%;
    display: flex; flex-direction: column;
  }
  .edge-strip .strip-white { flex: 0 0 45%; background: var(--white); }
  .edge-strip .strip-red { flex: 1; background: var(--red); }

  .brand { position: absolute; left: 56px; top: 52px; }
  .brand-row { display: flex; align-items: center; gap: 14px; }
  .brand-mark { width: 30px; height: 30px; background: var(--red); }
  .brand-name {
    font-weight: 900; font-size: 40px; letter-spacing: 1px;
    text-transform: uppercase; color: var(--white); line-height: 1;
  }
  .brand-tagline {
    margin-top: 6px; margin-left: 44px;
    font-weight: 300; font-size: 11px; letter-spacing: 3.2px;
    text-transform: uppercase; color: var(--white);
  }

  .address {
    position: absolute; right: 64px; top: 58px; text-align: right;
    font-size: 18px; line-height: 1.5; color: var(--text-light);
    font-style: normal;
  }

  .divider {
    position: absolute; left: 56px; right: 64px; top: 170px;
    height: 1px; background: var(--grey);
  }

  .contact { position: absolute; left: 56px; top: 210px; }
  .contact-name { color: var(--red); font-size: 28px; font-weight: 400; }
  .contact-title { font-size: 17px; margin-top: 4px; margin-bottom: 18px; }
  .contact-list { list-style: none; }
  .contact-list li {
    display: flex; align-items: center; gap: 12px;
    font-size: 17px; line-height: 1.75;
  }
  .contact-list svg { width: 16px; height: 16px; flex: none; }

  /* back */
  .back-content {
    position: absolute; inset: 0;
    display: flex; flex-direction: column; align-items: center; justify-content: center;
  }
  .back-brand-row { display: flex; align-items: center; gap: 18px; }
  .back-brand-mark { width: 40px; height: 40px; background: var(--white); }
  .back-brand-name {
    font-weight: 900; font-size: 62px; letter-spacing: 1px;
    text-transform: uppercase; line-height: 1;
  }
  .back-tagline {
    margin-top: 8px;
    font-weight: 300; font-size: 15px; letter-spacing: 5px; text-transform: uppercase;
  }
  .coupon {
    margin-top: 34px; font-size: 19px; font-weight: 300; letter-spacing: .5px;
  }
</style>
</head>
<body>

<section class="card card-front" aria-label="Business card front">
  <div class="edge-strip"><span class="strip-white"></span><span class="strip-red"></span></div>

  <div class="brand">
    <div class="brand-row">
      <span class="brand-mark"></span>
      <span class="brand-name">Quorvanex</span>
    </div>
    <div class="brand-tagline">Your Training Ally</div>
  </div>

  <address class="address">
    P.O. Box 47315<br>Harlow, Vermont 00000
  </address>

  <div class="divider"></div>

  <div class="contact">
    <div class="contact-name">Lorraine K. Vestal</div>
    <div class="contact-title">CEO</div>
    <ul class="contact-list">
      <li>
        <svg viewBox="0 0 16 16" aria-hidden="true"><path fill="#e8222b" d="M3.5 1.5l2.5 0 1 3.5-1.7 1.2a9 9 0 0 0 4.5 4.5l1.2-1.7 3.5 1v2.5c0 .8-.7 1.5-1.5 1.5A12.5 12.5 0 0 1 2 3c0-.8.7-1.5 1.5-1.5z"/></svg>
        555.417.3820
      </li>
      <li>
        <svg viewBox="0 0 16 16" aria-hidden="true"><rect x="1" y="3" width="14" height="10" rx="1" fill="#e8222b"/><path d="M1.5 3.8L8 9l6.5-5.2" fill="none" stroke="#111" stroke-width="1.3"/></svg>
        LVestal@Quorvanexco.com
      </li>
      <li>
        <svg viewBox="0 0 16 16" aria-hidden="true"><circle cx="8" cy="8" r="6.5" fill="none" stroke="#e8222b" stroke-width="1.5"/><ellipse cx="8" cy="8" rx="2.8" ry="6.5" fill="none" stroke="#e8222b" stroke-width="1.2"/><path d="M1.5 8h13" stroke="#e8222b" stroke-width="1.2"/></svg>
        www.quorvanexco.com
      </li>
    </ul>
  </div>
</section>

<section class="card card-back" aria-label="Business card back">
  <div class="back-content">
    <div class="back-brand-row">
      <span class="back-brand-mark"></span>
      <span class="back-brand-name">Quorvanex</span>
    </div>
    <div class="back-tagline">Your Training Ally</div>
    <p class="coupon">Sign up on our website for a coupon code</p>
  </div>
</section>

</body>
</html>
```